Bram Keystone Homes needs a business card

We need a business card for a new company in Canada, Ontario. Our company is all about luxury contraction homes for our clients. Our product and services are custom projects design. Under the business logo that will be created, we want a slogan that will be a memorable phrase for consumers to remember us to tell their friends and relatives.

Additional infomation
- Ludovic Entrasse
- President / Ceo
-519.604.3087

Find point what luxury construction products and services can be done

We like to see colors:
- #663300
- and something other colors or color that would attract the client needs and wants

The final design should communicate leads from new or old clients that will grow our empire. Most of all, we try to work among the budget that clients want

NOTE
- we also need an icon for the business (Example: Instagram, Facebook, and Whatsapp icons)
- We want the company name to be remembered easily for clients and our distributors who would get our orders.
- we need an icon on the business cards: Facebook and Instagram.

Thanks,
Bram Keystone Homes

```html
<!DOCTYPE html>
<html lang="en">
<head>
<meta charset="utf-8">
<title>Bram Keystone Homes – Business Card</title>
<link rel="stylesheet" href="https://fonts.googleapis.com/css2?family=Roboto:wght@400;500;700&family=Work+Sans:wght@400&display=swap">
<style>
  :root {
    --brown: #663300;
    --paper: #ffffff;
    --ink: #3a3a3a;
    --backdrop: #9a9a9a;
    --backdrop-light: #b4b4b4;
  }
  * { box-sizing: border-box; margin: 0; padding: 0; }
  html, body { width: 1200px; height: 930px; overflow: hidden; }
  body {
    background: radial-gradient(ellipse at 45% 40%, var(--backdrop-light), var(--backdrop));
    font-family: "Work Sans", sans-serif;
    position: relative;
  }
  .card {
    position: absolute;
    width: 560px;
    height: 320px;
    border-radius: 22px;
    box-shadow: 0 6px 18px rgba(0,0,0,0.28);
  }
  .card--front { left: 170px; top: 120px; background: var(--brown); }
  .card--back  { left: 470px; top: 490px; background: var(--paper); }

  .front-brand {
    position: absolute; inset: 0;
    display: flex; flex-direction: column; align-items: center; justify-content: center;
    color: var(--paper);
  }
  .front-brand__name {
    font-family: "Roboto", sans-serif;
    font-weight: 700;
    font-size: 40px;
    letter-spacing: 0.5px;
  }
  .front-brand__tagline {
    font-family: "Roboto", sans-serif;
    font-weight: 400;
    font-size: 14px;
    letter-spacing: 0.6px;
    margin-top: 6px;
  }

  .back-info {
    position: absolute; left: 0; right: 0; top: 108px;
    display: flex; align-items: center; justify-content: center; gap: 22px;
  }
  .person { text-align: right; }
  .person__name {
    font-family: "Roboto", sans-serif;
    font-weight: 500;
    font-size: 19px;
    color: var(--brown);
  }
  .person__role { font-size: 13px; color: var(--ink); margin-top: 2px; }
  .divider { width: 1.5px; height: 62px; background: var(--brown); }
  .contacts { list-style: none; font-size: 13px; color: var(--ink); line-height: 1.45; }
  .contacts li { display: flex; align-items: center; gap: 7px; }
  .contacts svg { width: 10px; height: 10px; flex: none; }
  .address {
    position: absolute; left: 0; right: 0; bottom: 38px;
    text-align: center; font-size: 13px; color: var(--ink); letter-spacing: 0.3px;
  }
</style>
</head>
<body>
  <section class="card card--front">
    <div class="front-brand">
      <div class="front-brand__name">Bram Keystone Homes</div>
      <div class="front-brand__tagline">- HOME RENOVATIONS - CUSTOM PROJECT DESIGN -</div>
    </div>
  </section>

  <section class="card card--back">
    <div class="back-info">
      <div class="person">
        <div class="person__name">Ludovic Entrasse</div>
        <div class="person__role">President / Ceo</div>
      </div>
      <div class="divider"></div>
      <ul class="contacts">
        <li>
          <svg viewBox="0 0 10 10" aria-hidden="true"><path d="M2 1 L3.6 1 L4.2 3 L3.2 3.8 Q4 5.8 6.2 6.8 L7 5.8 L9 6.4 L9 8 Q8.6 9 7.4 9 Q1 8 1 2.4 Q1 1 2 1 Z" fill="var(--brown)"/></svg>
          519.604.3087
        </li>
        <li>
          <svg viewBox="0 0 10 10" aria-hidden="true"><rect x="1" y="2" width="8" height="6" fill="none" stroke="var(--brown)" stroke-width="1.2"/><path d="M1 2 L5 5.5 L9 2" fill="none" stroke="var(--brown)" stroke-width="1.2"/></svg>
          info@bramkeystone.com
        </li>
        <li>
          <svg viewBox="0 0 10 10" aria-hidden="true"><circle cx="5" cy="5" r="4" fill="var(--brown)"/><path d="M1 5 H9 M5 1 Q2.5 5 5 9 M5 1 Q7.5 5 5 9" fill="none" stroke="var(--paper)" stroke-width="0.7"/></svg>
          www.bramkeystone.com
        </li>
      </ul>
    </div>
    <div class="address">218 Alder Crescent Guelph, ON N1H 4T2</div>
  </section>
</body>
</html>
```